Dental Practice Website design

Design a new website for Brambleford Dental Practice.
Design should be warm, neutral in colour, with some small amount of bright colour if needed but kept to a minimum. Website should look professional, high end. Home page should be easy to navigate and simple for patients to be able to book online.
Logo in files along with some examples of websites that we like. Please ask if any further info needed.
Menu should have:
About
New Patients
Treatments
Fees
Contact Us

Industry/Entity Type

Dentistry

Number of Pages Required

4 page

Font styles to use
Sans Serif

Colors

Designer to choose colors to be used in the design.

Requirements
Must have
• Ravelle ratings badge, book online button,
Nice to have
• neutral, relaxing colours
Should not have
• harsh, bright colours!

```html
<!DOCTYPE html>
<html lang="en">
<head>
<meta charset="utf-8">
<title>Brambleford Dental Practice</title>
<link href="https://fonts.googleapis.com/css2?family=Poppins:wght@200;300;400;500;600;700&display=swap" rel="stylesheet">
<style>
:root{
  --blue:#1a7fc4;
  --blue-dark:#136aa6;
  --ink:#111418;
  --text:#2a2d31;
  --muted:#9aa0a6;
  --line:#d9d9d9;
  --topbar:#f4f3f1;
  --hero:#cfcfd0;
  --soft:#eceef0;
  --panel:#f3f2f0;
  --footer:#f1f1f1;
  --white:#ffffff;
  --black:#0c0c0c;
}
*{box-sizing:border-box;margin:0;padding:0}
html,body{width:1200px;height:4559px;overflow:hidden}
body{font-family:'Poppins',sans-serif;color:var(--text);background:var(--white);position:relative}
.abs{position:absolute}
section,header,footer,nav{position:relative;width:1200px}
.btn{display:inline-flex;align-items:center;justify-content:center;background:var(--blue);color:var(--white);font-weight:600;font-size:12px;letter-spacing:.3px;text-transform:uppercase;text-decoration:none}
.hl{color:var(--blue)}
.placeholder{position:absolute}

/* top bar */
.topbar{height:58px;background:var(--topbar)}
.topbar .contact{left:117px;top:20px;display:flex;gap:18px;font-size:11px;color:var(--ink)}
.topbar .contact span{display:flex;align-items:center;gap:7px}
.topbar .btn{left:862px;top:4px;width:218px;height:52px}

/* logo */
.brand{height:154px;display:flex;flex-direction:column;align-items:center;justify-content:center;border-bottom:1px solid #ececec}
.brand .name{font-weight:300;font-size:34px;letter-spacing:2px;color:#3a3a3a;line-height:1;text-transform:uppercase}
.brand .sub{font-weight:300;font-size:17px;letter-spacing:2px;color:#3a3a3a;margin-top:6px;text-transform:uppercase}

/* nav */
.mainnav{height:66px;border-bottom:1px solid #ececec}
.mainnav a{position:absolute;top:24px;font-size:12.5px;font-weight:500;color:var(--ink);text-decoration:none;transform:translateX(-50%)}
.mainnav a.active{color:var(--blue)}

/* hero */
.hero{height:421px;background:var(--hero)}
.hero .skyline{left:0;bottom:0;width:1200px;height:300px;background:linear-gradient(180deg,rgba(207,207,208,0) 0%,#bfc0c2 60%,#b3b4b6 100%)}
.hero h1{left:120px;top:92px;font-size:56px;font-weight:700;color:var(--white);text-shadow:0 2px 6px rgba(0,0,0,.35)}
.hero p{left:120px;top:168px;width:810px;font-size:10.5px;line-height:1.6;color:var(--ink)}
.hero .btn{left:118px;top:218px;width:188px;height:36px}

.callband{height:67px;background:var(--blue);display:flex;align-items:center;justify-content:center;color:#d9ecf8;font-size:30px;font-weight:300}

/* how it works */
.how{height:685px}
.eyebrow{font-size:16px;color:var(--ink);text-transform:uppercase}
.title{font-size:54px;font-weight:600;color:var(--ink);line-height:1.1}
.how .eyebrow{left:0;width:1200px;text-align:center;top:40px}
.how .title{left:0;width:1200px;text-align:center;top:64px}
.how .photo{left:549px;top:136px;width:531px;height:478px;background:radial-gradient(ellipse at 55% 45%,#e8dccf 0%,#eef0f2 45%,#ffffff 75%)}
.step{left:122px;display:flex;align-items:center;gap:12px;font-size:18px;font-weight:500;color:var(--blue)}
.how .desc{left:122px;top:274px;width:440px;font-size:16px;line-height:1.65;color:var(--ink)}
.how .rule{left:122px;width:427px;height:1px;background:#cfcfcf}
.how .btn{left:118px;top:516px;width:227px;height:49px}

/* services */
.services{height:705px;background:linear-gradient(90deg,#eceef0 0%,#e7e9ec 55%,#dfe3e7 100%)}
.services .doctor{right:0;top:0;width:457px;height:705px;background:radial-gradient(ellipse at 50% 30%,#d9c1a8 0%,#e6e2dd 30%,#eef0f2 60%,rgba(236,238,240,0) 80%)}
.services .eyebrow{left:117px;top:78px}
.services .title{left:117px;top:118px;font-size:52px;line-height:1.05}
.services .lead{left:117px;top:246px;font-size:15px;color:var(--ink)}
.card{top:307px;width:225px;height:233px;background:var(--white);border-radius:12px;padding:0 22px}
.card svg{position:absolute;left:22px;top:20px}
.card h3{position:absolute;left:22px;top:74px;font-size:14.5px;font-weight:600;color:var(--ink)}
.card p{position:absolute;left:22px;top:110px;width:185px;font-size:11.5px;line-height:1.75;color:var(--text)}
.card .more{position:absolute;left:22px;top:187px;display:flex;align-items:center;gap:8px;font-size:10px;font-weight:600;color:var(--blue)}
.rating{left:117px;top:568px}
.rating .rname{font-size:46px;font-weight:600;color:var(--blue);line-height:1}
.rating .rrow{display:flex;align-items:center;gap:8px;margin-top:4px;font-size:26px;font-weight:600;color:#6b6f73}
.stars{display:flex;gap:2px}

/* join */
.join{height:972px}
.join .title{left:0;top:52px;width:1200px;text-align:center;font-size:44px}
.join .copy{left:117px;top:127px;width:966px;text-align:center;font-size:14px;line-height:1.95;color:var(--ink)}
.ba{top:352px;height:324px;background:linear-gradient(90deg,#e6c79b 0%,#f1e1c9 50%,#f3efe8 100%)}
.ba.two{background:linear-gradient(90deg,#e2c9b4 0%,#f4eee8 50%,#e8cdb6 100%)}
.ba .split{position:absolute;left:50%;top:0;width:2px;height:100%;background:rgba(255,255,255,.8)}
.strip{top:699px;height:212px}
.strip.a{background:linear-gradient(135deg,#d7dde3 0%,#e9d2bd 50%,#4aa6df 100%)}
.strip.b{background:linear-gradient(135deg,#bdbfc3 0%,#e7d6c6 50%,#8a6a55 100%)}
.strip.c{background:linear-gradient(135deg,#cfd8df 0%,#e7c3b3 55%,#7aa5c4 100%)}
.strip.d{background:linear-gradient(135deg,#d3e3ec 0%,#f1dcc4 55%,#58b0e0 100%)}
.strip.e{background:linear-gradient(135deg,#d8e2ea 0%,#7bbfe5 100%)}

/* testimonial */
.testimonial{height:465px}
.testimonial .panel{left:117px;top:0;width:964px;height:419px;background:var(--panel);border-radius:24px}
.testimonial .eyebrow{left:0;width:1200px;text-align:center;top:72px}
.testimonial .title{left:0;width:1200px;text-align:center;top:104px;font-size:46px}
.testimonial blockquote{left:170px;top:170px;width:860px;text-align:center;font-size:15.5px;line-height:1.8;color:var(--ink)}
.testimonial .who{left:0;width:1200px;text-align:center;top:300px;font-size:17px;font-weight:600;color:var(--ink)}
.testimonial .role{left:0;width:1200px;text-align:center;top:328px;font-size:15px;color:#c9c9c9}
.dots{left:0;width:1200px;top:368px;display:flex;justify-content:center;gap:6px}
.dots i{width:14px;height:14px;border-radius:50%;background:#d2d2d2;display:block}

/* blog */
.blog{height:575px}
.blog .eyebrow{left:0;width:1200px;text-align:center;top:10px}
.blog .title{left:0;width:1200px;text-align:center;top:30px;font-size:46px}
.blog .lead{left:0;width:1200px;text-align:center;top:98px;font-size:14px;color:var(--ink)}
.post{top:145px;width:306px}
.post .img{height:172px;border-radius:16px}
.post h4{margin:18px 0 0 14px;font-size:14.5px;font-weight:500;line-height:1.35;color:var(--ink)}
.post h4.hl{color:var(--blue)}
.post p{margin:8px 0 0 12px;font-size:11px;line-height:1.55;color:var(--ink)}
.partners{left:117px;top:472px;width:964px;display:flex;justify-content:space-between;align-items:center}
.partners i{display:block;height:44px;border-radius:6px;background:#d8d8d8}

/* footer */
.site-footer{height:331px;background:var(--footer)}
.site-footer h5{font-size:16px;font-weight:600;color:var(--ink);text-transform:uppercase;line-height:24px}
.col{top:44px}
.col ul{list-style:none;margin-top:20px}
.col li{font-size:12.5px;color:var(--ink);line-height:27px}
.contact-list li{display:flex;align-items:center;gap:14px;font-size:14.5px;line-height:38px}
.follow{left:538px;top:210px;display:flex;align-items:center;gap:6px;font-size:12px;color:var(--ink)}
.follow i{display:block;width:30px;height:30px;border-radius:50%;background:var(--ink)}
.hours{left:796px;top:0;width:284px;height:331px;background:var(--blue);color:var(--white);padding:44px 0 0 29px}
.hours h5{color:var(--white)}
.hours ul{list-style:none;margin-top:12px}
.hours li{font-size:14.5px;line-height:34px}
.certs{left:117px;top:260px;display:flex;gap:14px;align-items:center}
.certs i{display:block;width:93px;height:47px;background:#ffffff;border:1px solid #dcdcdc}
.certs .rt{font-size:30px;font-weight:600;color:var(--blue);line-height:1}
.certs .rs{font-size:12px;font-weight:600;color:#6b6f73;display:flex;gap:4px;align-items:center}
.copyright{height:60px;background:var(--black);color:var(--white);display:flex;align-items:center;justify-content:center;font-size:11px;font-weight:500;letter-spacing:.3px}
</style>
</head>
<body>

<header class="topbar">
  <div class="abs contact">
    <span><svg width="16" height="16" viewBox="0 0 24 24" fill="none" stroke="#111" stroke-width="1.8"><path d="M5 3h4l2 5-2.5 1.5a11 11 0 0 0 6 6L16 13l5 2v4a2 2 0 0 1-2 2A17 17 0 0 1 3 5a2 2 0 0 1 2-2z"/></svg>+44 (0)20 7946 0321</span>
    <span><svg width="17" height="14" viewBox="0 0 24 18" fill="none" stroke="#111" stroke-width="1.8"><rect x="1" y="1" width="22" height="16"/><path d="M1 1l11 9 11-9"/></svg>hello@bramblefordental.co.uk</span>
  </div>
  <a class="btn abs" href="#">Book an Appointment</a>
</header>

<div class="brand">
  <div class="name">Brambleford</div>
  <div class="sub">Dental Practice</div>
</div>

<nav class="mainnav">
  <a class="active" href="#" style="left:221px">HOME</a>
  <a href="#" style="left:345px">ABOUT US</a>
  <a href="#" style="left:495px">NEW PATIENTS</a>
  <a href="#" style="left:655px">TREATMENTS</a>
  <a href="#" style="left:789px">FEES</a>
  <a href="#" style="left:927px">CONTACT US</a>
</nav>

<section class="hero">
  <div class="placeholder skyline" role="img" aria-label="Line drawing of the London skyline with Big Ben, the Gherkin, the London Eye and Tower Bridge"></div>
  <h1 class="abs">About Us</h1>
  <p class="abs">Lorem Ipsum is simply dummy text of the printing and typesetting industry. Lorem Ipsum has been the industry's standard dummy text ever since the 1500s, when an unknown printer took.</p>
  <a class="btn abs" href="#">Book an Appointment</a>
</section>

<div class="callband">Get in touch with us today +44 (0)20 7946 0321</div>

<section class="how">
  <div class="abs eyebrow">How it work</div>
  <h2 class="abs title"><span class="hl">What We Do for</span> Your Teeth</h2>
  <div class="placeholder photo" role="img" aria-label="Photo of a dental receptionist in a white coat on the phone, taking notes beside a laptop"></div>
  <div class="abs step" style="top:226px"><svg width="32" height="28" viewBox="0 0 32 28" fill="none" stroke="#1a7fc4" stroke-width="1.6"><rect x="2" y="4" width="28" height="22" rx="3"/><path d="M2 10h28M9 1v6M23 1v6"/><rect x="7" y="15" width="4" height="4"/></svg>Book an Appointment</div>
  <p class="abs desc">Lorem Ipsum has been the industry's standard dummy text ever since the 1500s, when an unknown printer took a galley of type.</p>
  <div class="abs rule" style="top:365px"></div>
  <div class="abs step" style="top:383px"><svg width="32" height="30" viewBox="0 0 32 30" fill="none" stroke="#1a7fc4" stroke-width="1.6"><circle cx="16" cy="7" r="4"/><path d="M2 26c4-2 8-6 12-6h8M22 20l6-4"/></svg>What conditions can manual therapy treat?</div>
  <div class="abs rule" style="top:434px"></div>
  <div class="abs step" style="top:446px"><svg width="32" height="28" viewBox="0 0 32 28" fill="none" stroke="#1a7fc4" stroke-width="1.6"><rect x="4" y="3" width="24" height="16"/><path d="M10 26h12M16 19v7M9 9h8M9 13h12"/></svg>Expert Care</div>
  <a class="btn abs" href="#">Book an Appointment</a>
</section>

<section class="services">
  <div class="placeholder doctor" role="img" aria-label="Photo of a smiling senior dentist in a white coat in a bright clinic"></div>
  <div class="abs eyebrow">Our Services</div>
  <h2 class="abs title"><span class="hl">High Quality</span><br>Services for You</h2>
  <p class="abs lead">Lorem Ipsum is simply dummy text of the printing and typesetting industry.</p>

  <article class="abs card" style="left:117px">
    <svg width="34" height="36" viewBox="0 0 34 36" fill="none" stroke="#1a7fc4" stroke-width="1.5"><path d="M9 10c-4 0-6 4-4 9l3 12c1 3 3 3 4 0l2-7 2 7c1 3 3 3 4 0l3-12c2-5 0-9-4-9-2 0-3 1-5 1s-3-1-5-1z"/><path d="M4 3h26"/></svg>
    <h3>General Dental Care</h3>
    <p>Lorem Ipsum is simply dummy text of the printing and typesetting industry.</p>
    <span class="more">Read More <svg width="18" height="18" viewBox="0 0 18 18"><circle cx="9" cy="9" r="9" fill="#1a7fc4"/><path d="M6 9h6M9.5 6l3 3-3 3" stroke="#fff" stroke-width="1.6" fill="none"/></svg></span>
  </article>
  <article class="abs card" style="left:363px">
    <svg width="34" height="36" viewBox="0 0 34 36" fill="none" stroke="#1a7fc4" stroke-width="1.5"><path d="M9 4c-4 0-6 4-4 9l3 12c1 3 3 3 4 0l2-7 2 7c1 3 3 3 4 0l3-12c2-5 0-9-4-9-2 0-3 1-5 1s-3-1-5-1z"/></svg>
    <h3>Dental Implants</h3>
    <p>Lorem Ipsum is simply dummy text of the printing and typesetting industry.</p>
    <span class="more">Read More <svg width="18" height="18" viewBox="0 0 18 18"><circle cx="9" cy="9" r="9" fill="#1a7fc4"/><path d="M6 9h6M9.5 6l3 3-3 3" stroke="#fff" stroke-width="1.6" fill="none"/></svg></span>
  </article>
  <article class="abs card" style="left:609px">
    <svg width="34" height="36" viewBox="0 0 34 36" fill="none" stroke="#1a7fc4" stroke-width="1.5"><path d="M9 4h16v8H9zM11 12v8h12v-8M14 20v12M20 20v12"/></svg>
    <h3>Cosmetic Dentistry</h3>
    <p>Lorem Ipsum is simply dummy text of the printing and typesetting industry.</p>
    <span class="more">Read More <svg width="18" height="18" viewBox="0 0 18 18"><circle cx="9" cy="9" r="9" fill="#1a7fc4"/><path d="M6 9h6M9.5 6l3 3-3 3" stroke="#fff" stroke-width="1.6" fill="none"/></svg></span>
  </article>
  <article class="abs card" style="left:856px">
    <svg width="34" height="36" viewBox="0 0 34 36" fill="none" stroke="#1a7fc4" stroke-width="1.5"><path d="M9 4c-4 0-6 4-4 9l2 8c1 3 3 3 4 0l2-5 2 5c1 3 3 3 4 0l2-8c2-5 0-9-4-9-2 0-3 1-4 1s-3-1-4-1z"/><path d="M4 28c6 4 20 4 26 0"/></svg>
    <h3>Teeth Whitening</h3>
    <p>Lorem Ipsum is simply dummy text of the printing and typesetting industry.</p>
    <span class="more">Read More <svg width="18" height="18" viewBox="0 0 18 18"><circle cx="9" cy="9" r="9" fill="#1a7fc4"/><path d="M6 9h6M9.5 6l3 3-3 3" stroke="#fff" stroke-width="1.6" fill="none"/></svg></span>
  </article>

  <div class="abs rating">
    <div class="rname">Ravelle</div>
    <div class="rrow">Ratings
      <span class="stars">
        <svg width="18" height="18" viewBox="0 0 24 24"><path d="M12 2l3 7h7l-5.5 4.5 2 7.5L12 17l-6.5 4 2-7.5L2 9h7z" fill="#f4b400"/></svg>
        <svg width="18" height="18" viewBox="0 0 24 24"><path d="M12 2l3 7h7l-5.5 4.5 2 7.5L12 17l-6.5 4 2-7.5L2 9h7z" fill="#f4b400"/></svg>
        <svg width="18" height="18" viewBox="0 0 24 24"><path d="M12 2l3 7h7l-5.5 4.5 2 7.5L12 17l-6.5 4 2-7.5L2 9h7z" fill="#f4b400"/></svg>
        <svg width="18" height="18" viewBox="0 0 24 24"><path d="M12 2l3 7h7l-5.5 4.5 2 7.5L12 17l-6.5 4 2-7.5L2 9h7z" fill="#f4b400"/></svg>
        <svg width="18" height="18" viewBox="0 0 24 24"><path d="M12 2l3 7h7l-5.5 4.5 2 7.5L12 17l-6.5 4 2-7.5L2 9h7z" fill="#f4b400"/></svg>
      </span>
    </div>
  </div>
</section>

<section class="join">
  <h2 class="abs title"><span class="hl">Join Our</span> Practice</h2>
  <p class="abs copy">If you're looking for an exceptional dental practice, we're here to help! Our team is made up of highly skilled professionals who are dedicated to ensuring that all our patients receive top-notch care in a welcoming and comfortable environment. Whether you need a routine examination or a more specialised treatment, we have all the resources to provide you with the best dental care possible. Our practice is always up-to-date with the latest techniques and technologies to make sure that our patients receive the best possible results.<br>We understand that dental care can be expensive which is why we offer affordable prices to ensure that everyone has access to quality care. If you'd like to learn more about our practice, please don't hesitate to contact us.</p>
  <div class="placeholder ba" style="left:117px;width:472px" role="img" aria-label="Before and after whitening photo of a smile"><span class="split"></span></div>
  <div class="placeholder ba two" style="left:605px;width:475px" role="img" aria-label="Before and after photo of a restored front tooth"><span class="split"></span></div>
  <div class="placeholder strip a" style="left:0;width:246px" role="img" aria-label="Photo of a shade guide held against a patient's teeth"></div>
  <div class="placeholder strip b" style="left:260px;width:273px" role="img" aria-label="Photo of a smiling patient in a dental chair"></div>
  <div class="placeholder strip c" style="left:549px;width:272px" role="img" aria-label="Photo of a dental examination with mirror and probe"></div>
  <div class="placeholder strip d" style="left:834px;width:272px" role="img" aria-label="Photo of a whitening shade guide beside a patient's smile"></div>
  <div class="placeholder strip e" style="left:1122px;width:78px" role="img" aria-label="Photo of a patient during treatment"></div>
</section>

<section class="testimonial">
  <div class="abs panel"></div>
  <div class="abs eyebrow">Testimonial</div>
  <h2 class="abs title"><span class="hl">What Our</span> Clients Say</h2>
  <blockquote class="abs">“ The choice of profession is very important. I made my choice. And I have never regretted about it.<br>I'm glad that my job is to help people to become a little healthier and<br>more beautiful “Dentist –<br>similar to parents, but they criticise yoour teeth instead of your lifestyle. ”</blockquote>
  <div class="abs who">Daniel Hartley</div>
  <div class="abs role">Dental Implants</div>
  <div class="abs dots"><i></i><i></i><i></i></div>
</section>

<section class="blog">
  <div class="abs eyebrow">Blogs</div>
  <h2 class="abs title"><span class="hl">Check Our</span> Latest Articles</h2>
  <p class="abs lead">Lorem Ipsum is simply dummy text of the printing.</p>
  <article class="abs post" style="left:117px">
    <div class="img" role="img" aria-label="Photo of a laughing patient during a check-up" style="background:linear-gradient(135deg,#5fa8d6 0%,#e9d3c0 55%,#2d6f9c 100%)"></div>
    <h4>The Importance of Regular Dental Check-Ups</h4>
    <p>Lorem Ipsum is simply dummy text of the printing and typesetting industry.</p>
  </article>
  <article class="abs post" style="left:448px">
    <div class="img" role="img" aria-label="Photo of a dentist treating a patient in a bright surgery" style="background:linear-gradient(135deg,#c9d6e0 0%,#e2c7b6 50%,#6ea3c7 100%)"></div>
    <h4 class="hl">Top 5 Benefits of Professional Teeth Whitening</h4>
    <p>Lorem Ipsum is simply dummy text of the printing and typesetting industry.</p>
  </article>
  <article class="abs post" style="left:775px">
    <div class="img" role="img" aria-label="Photo of a dentist examining a smiling patient" style="background:linear-gradient(135deg,#4f8fbf 0%,#d9c2b0 55%,#9fc4dc 100%)"></div>
    <h4 class="hl">Understanding Dental Implants: What You Need to Know</h4>
    <p>Lorem Ipsum is simply dummy text of the printing and typesetting industry.</p>
  </article>
  <div class="abs partners">
    <i style="width:120px"></i><i style="width:140px"></i><i style="width:120px"></i><i style="width:130px"></i><i style="width:110px"></i><i style="width:120px"></i>
  </div>
</section>

<footer class="site-footer">
  <div class="abs col" style="left:117px">
    <h5>Quick Links</h5>
    <ul><li>About</li><li>New Patients</li><li>Treatments</li><li>Fees</li><li>Contact Us</li></ul>
  </div>
  <div class="abs col" style="left:292px">
    <h5>Dental Departments</h5>
    <ul><li>Cosmetic Dentistry</li><li>Endodontics</li><li>Oral Surgery</li><li>General Dental Care</li><li>Pediatric Dentistry</li></ul>
  </div>
  <div class="abs col" style="left:538px">
    <h5>Contact Us</h5>
    <ul class="contact-list" style="margin-top:12px">
      <li><svg width="20" height="20" viewBox="0 0 24 24" fill="none" stroke="#111" stroke-width="1.6"><path d="M5 3h4l2 5-2.5 1.5a11 11 0 0 0 6 6L16 13l5 2v4a2 2 0 0 1-2 2A17 17 0 0 1 3 5a2 2 0 0 1 2-2z"/></svg>+44 (0)20 7946 0321</li>
      <li><svg width="20" height="16" viewBox="0 0 24 18" fill="none" stroke="#111" stroke-width="1.6"><rect x="1" y="1" width="22" height="16"/><path d="M1 1l11 9 11-9"/></svg>hello@bramblefordental.co.uk</li>
      <li><svg width="20" height="22" viewBox="0 0 24 26" fill="none" stroke="#111" stroke-width="1.6"><path d="M12 25s-8-9-8-15a8 8 0 0 1 16 0c0 6-8 15-8 15z"/><circle cx="12" cy="10" r="3"/></svg>12 Orchard Lane, UK</li>
    </ul>
  </div>
  <div class="abs follow">Follow me: <i></i><i></i><i></i><i></i></div>
  <div class="abs hours">
    <h5>Opening Hours</h5>
    <ul>
      <li>Monday : 08.00 - 10.00</li><li>Tuesday : 08.00 - 10.00</li><li>Wednesday : 08.00 - 10.00</li><li>Thursday : 08.00 - 10.00</li><li>Friday : 09.00 - 07.00</li><li>Saturday : 10.00 - 05.00</li><li>Sunday : 10.00 - 05.00</li>
    </ul>
  </div>
  <div class="abs certs">
    <i></i><i></i><i></i>
    <div><div class="rt">Ravelle</div><div class="rs">Ratings <span style="color:#f4b400">★★★★★</span></div></div>
  </div>
</footer>

<div class="copyright">COPYRIGHT © 2025 BRAMBLEFORD DENTAL PRACTICE. ALL RIGHTS RESERVED.</div>

</body>
</html>
```